Flyer for customer acquisition.

Hello, We are a sportmanagement agency from Germany and we need information flyers for customer acquisition. It should be DinA4 and should have a modern but serious design. I have uploaded a information sheet, where you can find the text and the composition, the flyer should have. I also uploaded Pictures / Images, which you can use. Of course you can use other suitable images. If they are not free, I will buy them later. On the bottom of the flyer there has been the contact information. You will find them in the download section, too. If you have questions, just write me. If I forgot something, I will update the letter :) Thank you very much!
Ich brauche zusätzliche Tage um durchzusehen

```html
<!DOCTYPE html>
<html lang="de">
<head>
<meta charset="utf-8">
<title>ELB-S Nachwuchsförderung Flyer</title>
<link rel="stylesheet" href="https://fonts.googleapis.com/css2?family=Orbitron:wght@700;900&family=Open+Sans:wght@400;600;700&display=swap">
<style>
  :root {
    --blue: #29a3dc;
    --blue-dark: #1b7fb0;
    --black: #0b0b0d;
    --ink: #151618;
    --grey: #4a4b4e;
    --grey-light: #8a8b8e;
    --silver: #cfd0d2;
    --white: #ffffff;
  }
  * { box-sizing: border-box; margin: 0; padding: 0; }
  html, body { width: 707px; height: 1200px; overflow: hidden; background: var(--black); }
  .flyer {
    position: relative; width: 707px; height: 1200px; overflow: hidden;
    background: linear-gradient(180deg, #121316 0%, #0a0a0c 100%);
    font-family: "Open Sans", Arial, sans-serif; color: var(--white);
  }
  .hero-photo {
    position: absolute; left: 0; top: 0; width: 707px; height: 400px;
    background:
      radial-gradient(ellipse 60% 30% at 20% 12%, rgba(200,225,255,.55), transparent 70%),
      radial-gradient(ellipse 45% 25% at 80% 22%, rgba(180,210,255,.4), transparent 70%),
      radial-gradient(ellipse 18% 45% at 52% 55%, rgba(190,200,215,.35), transparent 75%),
      linear-gradient(180deg, #1c2a44 0%, #1a2238 40%, #10182a 62%, #15301f 80%, #0b0d10 100%);
  }
  .brand-pennant { position: absolute; right: 18px; top: 0; width: 170px; height: 200px; }
  .brand-name {
    position: absolute; right: 18px; top: 118px; width: 170px; text-align: center;
    font-family: "Open Sans", Arial, sans-serif; font-weight: 700; font-size: 26px; color: var(--white);
  }
  .title {
    position: absolute; left: 40px; top: 262px; width: 650px;
    transform: rotate(-4.5deg); transform-origin: left bottom;
    font-family: "Orbitron", Arial, sans-serif; font-weight: 900; font-style: italic; line-height: 1;
  }
  .title-top { font-size: 25px; color: var(--white); letter-spacing: .5px; }
  .title-main { font-size: 52px; color: var(--blue); margin-top: 4px; letter-spacing: 1px; }
  .band { position: absolute; left: 0; top: 330px; width: 707px; height: 200px; }
  .claim { position: absolute; left: 0; top: 440px; width: 707px; text-align: center; }
  .claim-blue { font-family: "Orbitron", Arial, sans-serif; font-weight: 900; font-size: 35px; color: var(--blue); letter-spacing: 1px; }
  .claim-white { font-family: "Open Sans", Arial, sans-serif; font-weight: 400; font-size: 33px; color: var(--white); margin-top: 2px; }
  .services {
    position: absolute; left: 0; top: 586px; width: 707px;
    display: grid; grid-template-columns: repeat(3, 1fr); row-gap: 26px;
  }
  .service { text-align: center; }
  .service-head {
    height: 54px; display: flex; align-items: center; justify-content: center;
    background: linear-gradient(180deg, #3d3e42 0%, #232427 55%, #131416 100%);
    border-top: 1px solid #5a5b5e; margin: 0 1px;
    color: var(--blue); font-weight: 700; font-size: 12.5px; line-height: 1.25; padding: 0 10px;
  }
  .service-body { padding: 12px 22px 0; font-size: 12.3px; line-height: 1.55; color: #e8e8e8; min-height: 120px; }
  .footnotes {
    position: absolute; left: 30px; top: 1010px; width: 647px; text-align: center;
    font-size: 9.6px; line-height: 1.5; color: var(--blue);
  }
  .footer-band { position: absolute; left: 0; top: 1060px; width: 707px; height: 140px; }
  .contact {
    position: absolute; left: 0; top: 1150px; width: 707px; height: 50px;
    display: flex; align-items: center; justify-content: center; gap: 22px;
    font-weight: 700; color: var(--white);
  }
  .contact-item { display: flex; align-items: center; gap: 8px; font-size: 18px; }
  .contact-item.phone { font-size: 24px; }
  .divider { width: 1px; height: 24px; background: rgba(255,255,255,.7); }
  .icon { width: 18px; height: 18px; }
</style>
</head>
<body>
<div class="flyer">
  <div class="hero-photo" role="img" aria-label="Photo: young football player seen from behind holding a ball in a floodlit stadium"></div>

  <svg class="brand-pennant" viewBox="0 0 170 200" aria-hidden="true">
    <defs>
      <linearGradient id="pennantFill" x1="0" y1="0" x2="1" y2="1">
        <stop offset="0" stop-color="#3a3b3f"/>
        <stop offset=".55" stop-color="#1d1e21"/>
        <stop offset="1" stop-color="#5a5b60"/>
      </linearGradient>
    </defs>
    <polygon points="0,0 170,0 170,200 85,165 0,200" fill="#bfc0c3"/>
    <polygon points="5,0 165,0 165,192 85,159 5,192" fill="url(#pennantFill)"/>
  </svg>
  <div class="brand-name">ELB</div>

  <div class="title">
    <div class="title-top">ELB-S NACHWUCHSFÖRDERUNG</div>
    <div class="title-main">UND -MANGEMENT</div>
  </div>

  <svg class="band" viewBox="0 0 707 200" aria-hidden="true">
    <defs>
      <linearGradient id="greyPanel" x1="0" y1="0" x2="0" y2="1">
        <stop offset="0" stop-color="#5b5c60"/>
        <stop offset=".5" stop-color="#2b2c2f"/>
        <stop offset="1" stop-color="#0e0f11"/>
      </linearGradient>
    </defs>
    <polygon points="0,60 707,0 707,200 0,200" fill="url(#greyPanel)"/>
    <polygon points="0,72 150,72 185,50 345,50 378,78 707,58 707,70 382,90 340,62 190,62 155,84 0,84" fill="var(--silver)"/>
    <polygon points="0,60 150,60 185,38 345,38 378,66 707,40 707,56 382,80 340,50 190,50 155,72 0,72" fill="var(--blue)"/>
    <polygon points="0,0 707,0 707,40 378,66 345,38 185,38 150,60 0,60" fill="#0b0b0d" opacity=".85"/>
  </svg>

  <div class="claim">
    <div class="claim-blue">WIR BEGLEITEN DICH</div>
    <div class="claim-white">AUF DEINEM WEG ZUM PROFI</div>
  </div>

  <section class="services">
    <article class="service">
      <h3 class="service-head">KARRIEREPLANUNG</h3>
      <p class="service-body">Wir haben deine Karriere im Blick! In enger Absprache mit deinen Eltern und dir leiten wir die richtigen Maßnahmen und Schritte ein, um dein Ziel „Profifußballer“ zu realisieren</p>
    </article>
    <article class="service">
      <h3 class="service-head">STÄNDIGER<br>ANSPRECHPARTNER</h3>
      <p class="service-body">Egal um welchen Themen es sich handelt, wir sind für dich da! Ein vertrauensvolles und freundschaftliches Verhältnis ist uns besonders wichtig.</p>
    </article>
    <article class="service">
      <h3 class="service-head">Rechtsberatung/<br>Vertragsrecht</h3>
      <p class="service-body">Juristendeutsch und Kleingedrucktes? Kein Problem! Wir helfen dir den Durchblick zu behalten und holen immer das Beste für dich raus.</p>
    </article>
    <article class="service">
      <h3 class="service-head">AUSRÜSTUNG</h3>
      <p class="service-body">Wir besorgen dir deine Ausrüstung! Unsere Beziehungen zu den großen Sportartikelherstellern ermöglichen den Abschluss von Ausrüsterverträgen*.</p>
    </article>
    <article class="service">
      <h3 class="service-head">VORSORGE</h3>
      <p class="service-body">Verletzungen gehören leider zum Fußball dazu. Wir sichern dich ab, indem wir eine private Zusatzkrankenversicherung für dich abschließen.</p>
    </article>
    <article class="service">
      <h3 class="service-head">Kooperationspartner/<br>Netzwerk</h3>
      <p class="service-body">Ob Entscheidungsträger oder Experte, wir kennen die richtigen Leute. Zusätzlich bieten wir dir eine große Bandbreite an Leistungen, die du jederzeit in Anspruch nehmen kannst**.</p>
    </article>
  </section>

  <p class="footnotes">*Die Entscheidung über das Zustandekommen eines Ausrüstervertrags obliegt dem jeweiligen Sportartikelhersteller. Ist ein Abschluss aktuell nicht möglich, erhältst du von uns 2x pro Saison neue Fußballschuhe sowie weitere Ausrüstungsgegenstände.<br>**Personal Training, Athletik-Training, Ernährungsberatung, Sportpsychologische Betreuung, uvm.</p>

  <svg class="footer-band" viewBox="0 0 707 140" aria-hidden="true">
    <polygon points="0,50 220,50 255,28 470,28 505,50 707,8 707,140 0,140" fill="var(--silver)"/>
    <polygon points="0,62 220,62 255,40 470,40 505,62 707,20 707,140 0,140" fill="#1a1b1e"/>
    <polygon points="0,90 707,42 707,140 0,140" fill="var(--blue)"/>
  </svg>

  <div class="contact">
    <span class="contact-item">
      <svg class="icon" viewBox="0 0 18 18" aria-hidden="true"><circle cx="9" cy="9" r="8.5" fill="#fff"/><rect x="4.5" y="6" width="9" height="6.5" fill="none" stroke="var(--blue)" stroke-width="1.3"/><polyline points="4.5,6 9,9.5 13.5,6" fill="none" stroke="var(--blue)" stroke-width="1.3"/></svg>
      info@elb-s.de
    </span>
    <span class="divider"></span>
    <span class="contact-item">
      <svg class="icon" viewBox="0 0 18 18" aria-hidden="true"><circle cx="9" cy="9" r="8.5" fill="#fff"/><circle cx="9" cy="9" r="5" fill="none" stroke="var(--blue)" stroke-width="1.2"/><ellipse cx="9" cy="9" rx="2.2" ry="5" fill="none" stroke="var(--blue)" stroke-width="1.2"/><line x1="4" y1="9" x2="14" y2="9" stroke="var(--blue)" stroke-width="1.2"/></svg>
      www.elb-s.de
    </span>
    <span class="divider"></span>
    <span class="contact-item phone">
      <svg class="icon" viewBox="0 0 18 18" aria-hidden="true"><path d="M4 2.5 L7 2.5 L8 6 L6.2 7.3 C7 9.2 8.8 11 10.7 11.8 L12 10 L15.5 11 L15.5 14 C15.5 15 14.6 15.7 13.6 15.6 C8 15 3 10 2.4 4.4 C2.3 3.4 3 2.5 4 2.5 Z" fill="#fff"/></svg>
      07000/5550123
    </span>
  </div>
</div>
</body>
</html>
```